goal design

We are rolling out a goal for the next 3 years. the goal is as follows:
2014: $8 million gross profit, $1.25 million net income
2015: $12 million gross profit, $2.4 million net income
2016 $15 million gross profit, $4 million net income
We want a design that captures these numbers and that we can publish company wide that will quickly remind everyone of these goals. Our website is www.brackenfieldcrew.com. This will be an internal campaign. We will use the simple design to remind our people of our goals for the next 3 years. We will print it on mouse pads, shirts and things of this nature periodically to keep it front of mind for our people. So easy to remember, visually appealing and simple are good guidelines.
Updates
Target Market(s)
This is an internal campaign. it is to remind our people of our goals for the next few years so will be on little reminder items (i.e. cell phone covers, mouse pads, shirts, screen savers, etc).
Industry/Entity Type
It Company
Look and feel

```html
<!DOCTYPE html>
<html lang="en">
<head>
<meta charset="utf-8">
<title>Three-Year Goals</title>
<link rel="stylesheet" href="https://fonts.googleapis.com/css2?family=Oswald:wght@500;700&family=Questrial&display=swap">
<style>
  :root {
    --canvas: #ffffff;
    --green: #8dc63f;
    --blue: #29abe2;
    --pink: #d91c5c;
    --tile-text: #ffffff;
    --url-text: #1a1a1a;
    --tile-gap: #ffffff;
  }
  * { box-sizing: border-box; margin: 0; padding: 0; }
  html, body {
    width: 1200px;
    height: 999px;
    overflow: hidden;
    background: var(--canvas);
  }
  .goal-board {
    position: relative;
    width: 1200px;
    height: 999px;
  }
  .goal-tile {
    position: absolute;
    color: var(--tile-text);
    text-align: center;
    font-family: "Oswald", "Arial Narrow", sans-serif;
    font-weight: 700;
  }
  .goal-tile--2014 {
    left: 483px; top: 265px;
    width: 228px; height: 232px;
    border-radius: 44px;
    background: var(--green);
    padding-top: 17px;
    z-index: 1;
  }
  .goal-tile--2015 {
    left: 327px; top: 454px;
    width: 240px; height: 240px;
    background: var(--blue);
    border: 6px solid var(--tile-gap);
    border-radius: 50px;
    padding-top: 20px;
    z-index: 2;
  }
  .goal-tile--2016 {
    left: 633px; top: 447px;
    width: 240px; height: 240px;
    background: var(--pink);
    border: 6px solid var(--tile-gap);
    border-radius: 50px;
    padding-top: 17px;
    z-index: 2;
  }
  .goal-year {
    display: block;
    font-size: 70px;
    line-height: 80px;
    letter-spacing: 0.5px;
  }
  .goal-line {
    display: block;
    font-size: 17px;
    line-height: 31px;
    font-weight: 500;
    white-space: nowrap;
  }
  .goal-amount {
    font-size: 24px;
    font-weight: 700;
  }
  .goal-site {
    position: absolute;
    left: 0; right: 0;
    top: 700px;
    text-align: center;
    font-family: "Questrial", "Century Gothic", sans-serif;
    font-size: 27px;
    line-height: 34px;
    color: var(--url-text);
    letter-spacing: 0.3px;
  }
</style>
</head>
<body>
  <main class="goal-board">
    <section class="goal-tile goal-tile--2014">
      <span class="goal-year">2014</span>
      <span class="goal-line"><span class="goal-amount">$8</span> million gross</span>
      <span class="goal-line">profit</span>
      <span class="goal-line"><span class="goal-amount">$1.25</span> million net</span>
      <span class="goal-line">income</span>
    </section>
    <section class="goal-tile goal-tile--2015">
      <span class="goal-year">2015</span>
      <span class="goal-line"><span class="goal-amount">$12</span> million gross</span>
      <span class="goal-line">profit</span>
      <span class="goal-line"><span class="goal-amount">$2.4</span> million net</span>
      <span class="goal-line">income</span>
    </section>
    <section class="goal-tile goal-tile--2016">
      <span class="goal-year">2016</span>
      <span class="goal-line"><span class="goal-amount">$15</span> million gross</span>
      <span class="goal-line">profit</span>
      <span class="goal-line"><span class="goal-amount">$4</span> million net</span>
      <span class="goal-line">income</span>
    </section>
    <p class="goal-site">www.brackenfieldcrew.com</p>
  </main>
</body>
</html>
```